Velk Partners Building Business Cards

We need a business card that reflects our business as "Solar Experts" in San Diego. Browse our website www.velkpartners.example our License needs to be displayed as "CSLB# 3867140" our phone number is (619) 555-0187

Save thousands on your electric bills and increase the value of your home while helping to protect the environment. Our solar installation experts will help you design the system that's right for you, using only the highest quality equipment that will look great and give you ideal performance. Our goal is to make you energy independent, and get your electric bill to 0.

Paul Osterby
(619) 555-0187
paul@velkpartners.example

Target Market(s)

Home owners in san diego looking for solar

Industry/Entity Type

Solar Energy

Contact Information for Business Card

Paul Osterby
(619) 555-0187
paul@velkpartners.example

Font styles to use
Other font styles liked:
• Use our logo font

Requirements
Must have
• License needs to be displayed as "CSLB# 3867140" our phone number is (619) 555-0187
Nice to have
• Real images of rooftop home solar in san diego
Should not have
• our business address

```html
<!DOCTYPE html>
<html lang="en">
<head>
<meta charset="utf-8">
<title>Velk Partners Building – Business Cards</title>
<link rel="stylesheet" href="https://fonts.googleapis.com/css2?family=Source+Sans+3:ital,wght@0,400;0,600;0,700;1,400&display=swap">
<style>
  :root {
    --navy: #1a3c73;
    --sun: #f7b000;
    --ink: #4a4a4a;
    --paper: #ffffff;
    --rule: #c9c9c9;
    --backdrop: #3b3b3b;
  }
  * { margin: 0; padding: 0; box-sizing: border-box; }
  html, body {
    width: 1105px; height: 1200px; overflow: hidden;
    background: var(--backdrop);
    font-family: "Source Sans 3", Arial, sans-serif;
  }
  .sheet { position: relative; width: 1105px; height: 1200px; }

  .card {
    position: absolute; left: 193px; width: 720px; height: 410px;
    overflow: hidden;
  }
  .card--front { top: 167px; background: var(--paper); }
  .card--back { top: 623px; background: var(--navy); }

  /* Front */
  .brand-name {
    position: absolute; left: 60px; top: 180px; width: 300px;
    text-align: center; font-weight: 700; font-size: 31px; line-height: 1.1;
    color: var(--navy);
  }
  .divider {
    position: absolute; left: 384px; top: 109px; width: 1px; height: 200px;
    background: var(--rule);
  }
  .contact { position: absolute; left: 417px; top: 110px; }
  .contact__name { font-size: 26px; font-weight: 600; color: var(--navy); line-height: 1; }
  .contact__role { font-size: 20px; color: var(--sun); margin-top: 6px; line-height: 1; }
  .contact__license { font-size: 19px; color: var(--ink); margin-top: 24px; line-height: 1; }
  .contact__list { list-style: none; margin-top: 20px; }
  .contact__list li {
    display: flex; align-items: center; gap: 10px;
    font-size: 19px; color: var(--ink); line-height: 28px;
  }
  .contact__list svg { width: 16px; height: 16px; flex: none; fill: var(--navy); }

  .trim-line { position: absolute; left: 0; top: 377px; width: 100%; height: 3px; background: var(--sun); }
  .trim-band { position: absolute; left: 0; top: 382px; width: 100%; height: 28px; background: var(--navy); }

  /* Back */
  .back-mark {
    position: absolute; left: 0; top: 120px; width: 100%;
    display: flex; align-items: center; justify-content: center; gap: 18px;
  }
  .back-mark__dot { width: 56px; height: 56px; border-radius: 50%; background: var(--sun); }
  .back-mark__name { font-size: 40px; font-weight: 700; color: var(--paper); }
  .back-url {
    position: absolute; left: 0; top: 340px; width: 100%; text-align: center;
    font-size: 19px; font-style: italic; letter-spacing: 3.5px; color: var(--paper);
  }
</style>
</head>
<body>
<main class="sheet">
  <section class="card card--front">
    <div class="brand-name">Velk Partners Building</div>
    <div class="divider"></div>
    <div class="contact">
      <div class="contact__name">Paul Osterby</div>
      <div class="contact__role">CEO/Founder</div>
      <div class="contact__license">CSLB# 3867140</div>
      <ul class="contact__list">
        <li>
          <svg viewBox="0 0 16 16" aria-hidden="true"><path d="M3.6 1.2l2.3 2.6-1.3 1.9c.9 2 2.5 3.6 4.5 4.6l1.9-1.3 2.7 2.3-1.3 2.7C6.6 14.6 1.4 9.4 1 3.5z"/></svg>
          (619) 555-0187
        </li>
        <li>
          <svg viewBox="0 0 16 16" aria-hidden="true"><path d="M1 3.5h14v9H1z M1.8 4.3L8 9l6.2-4.7" fill="none" stroke="#1a3c73" stroke-width="1.4"/><path d="M1 3.5h14L8 8.6z"/></svg>
          paul@velkpartners.example
        </li>
        <li>
          <svg viewBox="0 0 16 16" aria-hidden="true"><circle cx="8" cy="8" r="7"/><path d="M1 8h14M8 1c2.5 2.2 2.5 11.8 0 14M8 1c-2.5 2.2-2.5 11.8 0 14" fill="none" stroke="#fff" stroke-width="1"/></svg>
          www.velkpartners.example
        </li>
      </ul>
    </div>
    <div class="trim-line"></div>
    <div class="trim-band"></div>
  </section>

  <section class="card card--back">
    <div class="back-mark">
      <span class="back-mark__dot"></span>
      <span class="back-mark__name">Velk Partners Building</span>
    </div>
    <div class="back-url">www.velkpartners.example</div>
  </section>
</main>
</body>
</html>
```